Website design for Puddle Jump Kidscare

I need a website designed for my daycare business, Puddle Jump Kidscare, now that I have a new logo. My former website was ok but simple and I did not have a logo yet. It also was created by me using a template and was entirely pink. I loved the bright, happy feel of it but worried it might not appeal as much to potential clients who have sons. Therefore, I need a site which will appeal to both genders while still keeping the cheerful color scheme of my new logo, which has pinks, blue, green and cream.
Updates

Reason: Hello! I am still trying to download my new logo and am sorry it is taking me so long. Hopefully I will it posted by the end of today (US Eastern Standard Time). Thank you all very much for your patience!

Hello! I have finally managed to upload my new logo for you to use in designing my website. I'm sorry it took so long and greatly appreciate your time and creative efforts! I look forward to seeing what is submitted based on my logo design and its style/colors.

Many thanks!

Reason: As I've been traveling and posted my logo file late, I am extending my deadline. I am now back and can focus on providing more and better feedback. I appreciate your patience and submissions very much!

Reason: I need more time to provide feedback and make decisions.

Industry/Entity Type

Daycare

Colors
0192cd
33a6d7
86cae7
cadf82
fbf289
add136
e34197

```html
<!DOCTYPE html>
<html lang="en">
<head>
<meta charset="utf-8">
<title>Puddle Jump Kidscare</title>
<link href="https://fonts.googleapis.com/css2?family=Arimo:ital,wght@0,400;0,700;1,400&display=swap" rel="stylesheet">
<style>
:root{
  --pink:#cf7597;
  --pink-dark:#bd6485;
  --pink-text:#d2577f;
  --button-top:#e58bab;
  --button-bottom:#cf6a8e;
  --blue:#1a9fd0;
  --news-bg:#eeeff2;
  --body-text:#4a4a4a;
  --green:#7aae4f;
  --footer:#2d2d2d;
  --footer-text:#d6d6d6;
  --icon:#7d7d7d;
  --white:#ffffff;
}
*{margin:0;padding:0;box-sizing:border-box}
html,body{width:882px;height:1200px;overflow:hidden;background:var(--white)}
body{position:relative;font-family:"Arimo",Arial,sans-serif;color:var(--body-text)}
.abs{position:absolute}

/* header */
.site-header{left:0;top:0;width:882px;height:54px;background:var(--pink)}
.brand{left:126px;top:15px;font-size:19px;font-weight:700;color:var(--white);white-space:nowrap}
.nav-item{top:0;height:54px;line-height:54px;font-size:9px;color:var(--white);text-align:center}
.nav-item.active{background:var(--pink-dark)}

/* hero */
.hero{left:0;top:54px;width:882px;height:360px;background:linear-gradient(180deg,#5ea8e0 0%,#a8cff0 38%,#c9a88f 62%,#6f9a47 88%,#4f8a32 100%)}
.hero-arrow{top:212px}
.caption{background:rgba(20,20,20,.78);color:var(--white);font-size:12px;padding:0 14px;white-space:nowrap}
.caption-title{left:126px;top:304px;height:30px;line-height:30px}
.caption-line{left:126px;top:340px;height:30px;line-height:30px}

/* news */
.news{left:0;top:414px;width:882px;height:74px;background:var(--news-bg);border-bottom:1px solid #dcdde0}
.news-title{left:126px;top:427px;font-size:11px;color:var(--pink-text)}
.news-text{left:127px;top:446px;width:476px;font-size:7.5px;line-height:15px;color:#555}
.news-arrows{left:588px;top:429px}
.more-button{left:623px;top:434px;width:131px;height:34px;border-radius:2px;border:1px solid #c45f84;background:linear-gradient(var(--button-top),var(--button-bottom));color:var(--white);font-size:10.5px;text-align:center;line-height:32px}

/* welcome */
.welcome-title{left:0;top:518px;width:882px;text-align:center;font-size:14px;line-height:19px;color:var(--blue)}
.welcome-text{left:148px;top:570px;width:586px;text-align:center;font-size:8px;line-height:17px;color:var(--body-text)}

/* features */
.feature-image{top:646px;width:195px;height:132px}
.img-learning{left:126px;background:linear-gradient(135deg,#c96a3c,#e9a35d 45%,#3d6fb4)}
.img-creativity{left:344px;background:linear-gradient(160deg,#efe9e6,#e6c9d4 45%,#d94d8b 70%,#3a7fc4)}
.img-sharing{left:562px;background:linear-gradient(135deg,#7cb2dd,#c7363c 45%,#f0c742 75%,#5c8e3a)}
.feature-title{top:792px;font-size:12.5px;color:var(--blue)}
.feature-text{top:815px;width:185px;font-size:7.2px;line-height:14.5px;color:var(--body-text)}

/* testimonials */
.clients{left:0;top:917px;width:882px;height:211px;background:var(--green)}
.clients-title{left:0;top:946px;width:882px;text-align:center;font-size:15px;color:var(--white)}
.quote-mark{font-size:34px;line-height:1;color:#b6d497;font-family:Georgia,serif}
.clients-text{left:214px;top:983px;width:454px;text-align:center;font-size:7.8px;line-height:16px;color:var(--white)}
.client-name{left:0;top:1073px;width:882px;text-align:center;font-size:8px;color:var(--white)}
.client-date{left:0;top:1087px;width:882px;text-align:center;font-size:8px;font-style:italic;color:var(--white)}
.slide-arrow{top:1013px}

/* footer */
.site-footer{left:0;top:1128px;width:882px;height:72px;background:var(--footer)}
.footer-nav{left:128px;top:1149px;font-size:7.5px;color:var(--footer-text);white-space:nowrap;word-spacing:1px}
.footer-nav .sep{margin:0 11px}
.copyright{left:128px;top:1170px;font-size:7.5px;color:var(--footer-text)}
.social{left:627px;top:1155px}
</style>
</head>
<body>

<header class="site-header abs">
  <div class="brand abs">Puddle Jump Kidscare</div>
  <nav>
    <div class="nav-item active abs" style="left:328px;width:68px">About Us</div>
    <div class="nav-item abs" style="left:402px;width:54px">Services</div>
    <div class="nav-item abs" style="left:470px;width:80px">Hours and Fees</div>
    <div class="nav-item abs" style="left:560px;width:52px">Policies</div>
    <div class="nav-item abs" style="left:628px;width:48px">Photos</div>
    <div class="nav-item abs" style="left:698px;width:66px">Testimonials</div>
  </nav>
</header>

<section class="hero abs" role="img" aria-label="Photo of happy children and parents jumping on a grassy field under a blue sky"></section>
<svg class="hero-arrow abs" style="left:50px" width="33" height="33" viewBox="0 0 33 33" aria-hidden="true">
  <circle cx="16.5" cy="16.5" r="15" fill="rgba(255,255,255,.15)" stroke="rgba(255,255,255,.7)" stroke-width="1.5"/>
  <path d="M19 9 L11 16.5 L19 24 Z" fill="rgba(255,255,255,.7)"/>
</svg>
<svg class="hero-arrow abs" style="left:800px" width="33" height="33" viewBox="0 0 33 33" aria-hidden="true">
  <circle cx="16.5" cy="16.5" r="15" fill="rgba(255,255,255,.15)" stroke="rgba(255,255,255,.7)" stroke-width="1.5"/>
  <path d="M14 9 L22 16.5 L14 24 Z" fill="rgba(255,255,255,.7)"/>
</svg>
<div class="caption caption-title abs">PUDDLE JUMP KIDSCARE</div>
<div class="caption caption-line abs">A PLAYSPACE WHERE CHILDREN CAN PLAY, CREATE, AND IMAGINE!</div>

<section class="news abs"></section>
<h3 class="news-title abs" style="font-weight:400">Latest News</h3>
<svg class="news-arrows abs" width="16" height="8" viewBox="0 0 16 8" aria-hidden="true">
  <path d="M4 1 L1 4 L4 7" fill="none" stroke="#999" stroke-width="1"/>
  <path d="M12 1 L15 4 L12 7" fill="none" stroke="#999" stroke-width="1"/>
</svg>
<p class="news-text abs">We are thrilled to have found a new cheerful space with a private backyard! It's large, sunny, and filled with outdoor play equipment such as a toddler slide, sand/water activity table, and lots of toys! Please stay...</p>
<div class="more-button abs">Click here for more</div>

<h1 class="welcome-title abs" style="font-weight:400">Welcome to Puddle Jump Kidscare,<br>a playspace where children can play, create, and imagine!</h1>
<p class="welcome-text abs">Welcome to Puddle Jump Kidscare, a licensed Group Family Day Care, located in Harborview's leafy Elm Hill district. We are located on a pretty, tree-lined block on Larkspur Street, between Birch and Cedar Avenues. We are a few blocks from the Green Line tram and the Route 12 bus line, and we offer flexible hourly childcare, making it as easy as possible for busy parents on the go to arrange their children's care.</p>

<div class="feature-image img-learning abs" role="img" aria-label="Photo of two children reading a book together"></div>
<div class="feature-image img-creativity abs" role="img" aria-label="Photo of toddlers playing with building blocks on a foam mat"></div>
<div class="feature-image img-sharing abs" role="img" aria-label="Photo of smiling children lying in a circle on the grass"></div>

<h2 class="feature-title abs" style="left:127px;font-weight:400">Learning</h2>
<p class="feature-text abs" style="left:127px">We develop age-appropriate activities that introduce and strengthen academic and social skills.</p>
<h2 class="feature-title abs" style="left:345px;font-weight:400">Creativity</h2>
<p class="feature-text abs" style="left:345px">We offer children a wide range of creative opportunities including art projects, toddler yoga lessons, afternoon tea parties, dress up play, and a large selection of books and games.</p>
<h2 class="feature-title abs" style="left:563px;font-weight:400">Sharing</h2>
<p class="feature-text abs" style="left:563px;top:813px">We strive to include enrichment activities that extend your child's understanding of the world and their role in it. During our tea parties, for instance, we teach and emphasize good manners so that your child can learn their benefits as they grow.</p>

<section class="clients abs"></section>
<h2 class="clients-title abs" style="font-weight:400">What Clients Say</h2>
<div class="quote-mark abs" style="left:183px;top:972px">&ldquo;</div>
<div class="quote-mark abs" style="left:680px;top:1038px">&rdquo;</div>
<p class="clients-text abs">We would love to hear from you if your child has come to Puddle Jump! If you would like to leave a testimonial, please complete the Contact Us form on this page so we may post your message below. We would love to hear from you if your child has come to Puddle Jump! If you would like to leave a testimonial, please complete the Contact Us form on this page so we may post your message below.</p>
<div class="client-name abs">Marcus Ellery</div>
<div class="client-date abs">Posted on 27 Mar 2014</div>
<svg class="slide-arrow abs" style="left:130px" width="9" height="18" viewBox="0 0 9 18" aria-hidden="true"><path d="M8 1 L1 9 L8 17" fill="none" stroke="#b6d497" stroke-width="1.2"/></svg>
<svg class="slide-arrow abs" style="left:742px" width="9" height="18" viewBox="0 0 9 18" aria-hidden="true"><path d="M1 1 L8 9 L1 17" fill="none" stroke="#b6d497" stroke-width="1.2"/></svg>

<footer class="site-footer abs"></footer>
<div class="footer-nav abs">Home<span class="sep">|</span>About Us<span class="sep">|</span>Services<span class="sep">|</span>Hours and Fees<span class="sep">|</span>Policies<span class="sep">|</span>Contact Us<span class="sep">|</span>Photos<span class="sep">|</span>Testimonials</div>
<div class="copyright abs">© Copyright. Puddle Jump Kidscare. 2014. All Rights Reserved.</div>
<svg class="social abs" width="130" height="22" viewBox="0 0 130 22" aria-label="Social links">
  <circle cx="11" cy="11" r="10" fill="var(--icon)"/>
  <circle cx="38" cy="11" r="10" fill="var(--icon)"/>
  <circle cx="65" cy="11" r="10" fill="var(--icon)"/>
  <circle cx="92" cy="11" r="10" fill="var(--icon)"/>
  <circle cx="119" cy="11" r="10" fill="var(--icon)"/>
</svg>

</body>
</html>
```